Bluecrest Learning Corps by graduating students from college in two years

Based on the logo design, create stationary and business cards for
Dr. Venrel T Oskamp, CEO, (541) 482-1736
and Marisa Deltoft, Respresentative, (458) 647-2208
Address: 4719 Pellham Court, Corvan Ridge, OR 97218
Incorporate elelments of the logo

Target Market(s)

USA

Font styles to use
Other font styles liked:
• match with the logo type style

```html
<!DOCTYPE html>
<html lang="en">
<head>
<meta charset="utf-8">
<title>Bluecrest Learning Corps – Business Cards</title>
<link rel="stylesheet" href="https://fonts.googleapis.com/css2?family=Open+Sans:wght@400;700&display=swap">
<style>
  :root {
    --navy: #0a1f63;
    --navy-deep: #061650;
    --royal: #12329a;
    --gold: #f2bd22;
    --paper: #ffffff;
    --ink-grey: #6b6b6b;
    --rule-grey: #8a8a8a;
    --backdrop: #e9e9e9;
  }
  * { margin: 0; padding: 0; box-sizing: border-box; }
  html, body {
    width: 1200px;
    height: 801px;
    overflow: hidden;
    background: var(--backdrop);
    font-family: "Open Sans", Arial, sans-serif;
  }
  .canvas {
    position: relative;
    width: 1200px;
    height: 801px;
  }
  .card {
    position: absolute;
    top: 250px;
    width: 530px;
    height: 303px;
    overflow: hidden;
    box-shadow: 0 10px 24px rgba(0, 0, 0, 0.18);
  }
  /* ---------- front ---------- */
  .card-front {
    left: 45px;
    background: var(--paper);
  }
  .front-brand {
    position: absolute;
    left: 28px;
    top: 74px;
    width: 200px;
    display: flex;
    align-items: center;
    gap: 10px;
  }
  .brand-dot {
    flex: none;
    width: 22px;
    height: 22px;
    border-radius: 50%;
    background: var(--navy);
  }
  .brand-name {
    font-weight: 700;
    font-size: 19px;
    line-height: 1.2;
    color: var(--navy);
  }
  .front-divider {
    position: absolute;
    left: 245px;
    top: 42px;
    width: 1px;
    height: 160px;
    background: var(--rule-grey);
  }
  .contacts {
    position: absolute;
    left: 270px;
    top: 40px;
  }
  .contact + .contact { margin-top: 18px; }
  .contact-name {
    font-weight: 700;
    font-size: 19px;
    line-height: 1.15;
    color: var(--navy);
  }
  .contact-role {
    font-size: 14px;
    line-height: 1.3;
    color: var(--ink-grey);
  }
  .contact-phone {
    display: flex;
    align-items: center;
    gap: 6px;
    font-size: 14px;
    line-height: 1.3;
    color: var(--ink-grey);
  }
  .phone-icon { width: 14px; height: 14px; flex: none; }
  .address-band {
    position: absolute;
    left: 0;
    bottom: 0;
    width: 100%;
    height: 58px;
    background: var(--navy);
    border-top: 3px solid var(--gold);
    box-shadow: 0 -4px 0 var(--paper), 0 -5px 0 var(--gold);
    display: flex;
    align-items: center;
    padding-left: 30px;
    color: var(--paper);
    font-size: 17px;
    letter-spacing: 0.3px;
  }
  /* ---------- back ---------- */
  .card-back {
    left: 625px;
  }
  .cap-pattern {
    position: absolute;
    inset: 0;
    background: linear-gradient(135deg, var(--navy-deep) 0%, var(--navy) 45%, var(--royal) 100%);
  }
  .back-brand {
    position: absolute;
    inset: 0;
    display: flex;
    align-items: center;
    justify-content: center;
    gap: 14px;
  }
  .back-brand .brand-dot {
    width: 30px;
    height: 30px;
    background: var(--gold);
  }
  .back-brand .brand-name {
    font-size: 26px;
    color: var(--paper);
  }
</style>
</head>
<body>
<main class="canvas">

  <section class="card card-front" aria-label="Business card front">
    <div class="front-brand">
      <span class="brand-dot"></span>
      <span class="brand-name">Bluecrest Learning Corps</span>
    </div>

    <div class="front-divider"></div>

    <div class="contacts">
      <div class="contact">
        <p class="contact-name">Dr. Venrel T Oskamp</p>
        <p class="contact-role">CEO</p>
        <p class="contact-phone">
          <svg class="phone-icon" viewBox="0 0 24 24" aria-hidden="true">
            <path fill="#f2bd22" d="M6.6 10.8a15.1 15.1 0 0 0 6.6 6.6l2.2-2.2a1 1 0 0 1 1-.25 11.4 11.4 0 0 0 3.6.57 1 1 0 0 1 1 1V20a1 1 0 0 1-1 1A17 17 0 0 1 3 4a1 1 0 0 1 1-1h3.5a1 1 0 0 1 1 1c0 1.25.2 2.45.57 3.57a1 1 0 0 1-.25 1z"/>
          </svg>
          (541) 482-1736
        </p>
      </div>
      <div class="contact">
        <p class="contact-name">Marisa Deltoft</p>
        <p class="contact-role">Respresentative</p>
        <p class="contact-phone">
          <svg class="phone-icon" viewBox="0 0 24 24" aria-hidden="true">
            <path fill="#f2bd22" d="M6.6 10.8a15.1 15.1 0 0 0 6.6 6.6l2.2-2.2a1 1 0 0 1 1-.25 11.4 11.4 0 0 0 3.6.57 1 1 0 0 1 1 1V20a1 1 0 0 1-1 1A17 17 0 0 1 3 4a1 1 0 0 1 1-1h3.5a1 1 0 0 1 1 1c0 1.25.2 2.45.57 3.57a1 1 0 0 1-.25 1z"/>
          </svg>
          (458) 647-2208
        </p>
      </div>
    </div>

    <div class="address-band">4719 Pellham Court, Corvan Ridge, OR 97218</div>
  </section>

  <section class="card card-back" aria-label="Business card back">
    <div class="cap-pattern" role="img" aria-label="Navy background with a faint repeating pattern of graduation caps"></div>
    <div class="back-brand">
      <span class="brand-dot"></span>
      <span class="brand-name">Bluecrest Learning Corps</span>
    </div>
  </section>

</main>
</body>
</html>
```